Haulage company, lets use ruby red white and some 3rd color for web design. and Garvel Pryce Transport logo

Target Market(s)

Transport industry

Industry/Entity Type

transport

Number of Pages Required

2 page

Requirements
Must have
• Logo

```html
<!DOCTYPE html>
<html lang="en">
<head>
<meta charset="utf-8">
<title>Garvel Pryce Transport</title>
<link href="https://fonts.googleapis.com/css2?family=Roboto:wght@400;500;700&display=swap" rel="stylesheet">
<style>
:root{
  --ruby:#8c1020;
  --ruby-dark:#6e0c18;
  --frame:#b0424f;
  --ink:#111;
  --muted:#555;
  --grey-bg:#f1f1f1;
  --white:#fff;
}
*{margin:0;padding:0;box-sizing:border-box}
html,body{width:1200px;height:3830px;overflow:hidden}
body{font-family:'Roboto',Arial,sans-serif;color:var(--ink);background:var(--white);position:relative}
.abs{position:absolute}
.topbar{left:0;top:0;width:1200px;height:9px;background:var(--ruby)}
.header{left:0;top:9px;width:1200px;height:83px;background:var(--white)}
.brand{left:110px;top:34px;font-size:24px;font-weight:700;color:var(--ruby)}
.nav{right:110px;top:40px;display:flex;gap:38px;font-size:15px;align-items:center}
.hero{left:0;top:92px;width:1200px;height:558px;background:linear-gradient(180deg,#6d3a55 0%,#4b2a3e 40%,#2d1b26 100%)}
.hero-truck{left:25px;top:90px;width:470px;height:370px;background:linear-gradient(135deg,#e6e6ea,#9a2b3e);border-radius:6px}
.hero-road{left:560px;top:200px;width:640px;height:340px;background:linear-gradient(160deg,transparent 30%,rgba(200,40,70,.45) 60%,transparent 80%)}
.hero-text{left:664px;top:188px;color:#fff;width:420px}
.hero-text .pre{font-size:25px;font-weight:500}
.hero-text h1{font-size:42px;font-weight:700;margin:14px 0 20px;white-space:nowrap}
.hero-text p{font-size:15px;line-height:23px;text-align:justify}
h2.section-title{font-size:38px;font-weight:700;color:var(--ruby)}
.about-title{left:110px;top:728px}
.about-lead{left:110px;top:796px;width:458px;font-size:18px;font-weight:500;line-height:26px;text-align:justify}
.body-text{font-size:13.5px;line-height:21.5px;color:var(--muted);text-align:justify}
.about-p1{left:110px;top:860px;width:458px}
.about-p2{left:110px;top:956px;width:458px}
.btn{background:var(--ruby);color:#fff;font-size:16px;width:162px;height:42px;display:flex;align-items:center;justify-content:center}
.about-btn{left:110px;top:1098px}
.about-frame{left:654px;top:755px;width:431px;height:385px;background:var(--frame)}
.about-photo{left:635px;top:736px;width:431px;height:385px;background:linear-gradient(180deg,#c9d6e3 0%,#dfe4e9 45%,#9a9c98 100%)}
.services{left:0;top:1227px;width:1200px;height:569px;background:radial-gradient(circle at 70% 20%,#9e1525,var(--ruby) 60%,var(--ruby-dark))}
.services-title{left:0;top:1305px;width:1200px;text-align:center;color:#fff;font-size:40px;font-weight:700}
.card{top:1395px;width:306px;height:282px}
.card-label{top:1653px;width:262px;height:57px;background:#fff;font-size:23px;font-weight:500;display:flex;align-items:center;justify-content:center}
.arrow{top:1515px}
.why-frame{left:110px;top:1899px;width:418px;height:348px;background:var(--frame)}
.why-photo{left:131px;top:1884px;width:415px;height:346px;background:linear-gradient(180deg,#1b1f24,#3a3a3a 60%,#2a2622)}
.why-title{left:601px;top:1926px}
.why-p1{left:601px;top:1996px;width:485px}
.why-p2{left:601px;top:2071px;width:485px}
.why-btn{left:601px;top:2157px}
.testimonials{left:0;top:2333px;width:1200px;height:614px;background:radial-gradient(circle at 30% 60%,#f7f7f7,var(--grey-bg))}
.testi-title{left:0;top:2412px;width:1200px;text-align:center}
.avatar{top:2512px;width:137px;height:137px;border-radius:50%;background:linear-gradient(180deg,#c9c9c9,#6f6f6f)}
.quote{top:2686px;width:300px;text-align:center;font-size:14.5px;line-height:26px;letter-spacing:.8px;color:#333}
.quote-name{top:2767px;width:300px;text-align:center;font-size:21px;font-weight:500;letter-spacing:1.5px}
.dots{left:546px;top:2842px;display:flex;gap:9px}
.dot{width:19px;height:19px;border-radius:50%;background:#c8c8c8}
.dot.active{background:var(--ruby)}
.faq-title{left:110px;top:3024px}
.faq-rule{left:110px;top:3079px;width:101px;height:2px;background:var(--ruby)}
.faq-line{left:135px;top:3190px;width:0;height:300px;border-left:1px dashed #bbb}
.faq-q{left:182px;font-size:16px;font-weight:500}
.faq-a{left:182px;top:3188px;width:425px;font-size:13.5px;line-height:21.5px;color:var(--muted)}
.faq-art{left:639px;top:3182px;width:454px;height:268px;background:radial-gradient(ellipse at center,#f4f4f4,#fff 70%)}
.footer{left:0;top:3590px;width:1200px;height:240px;background:radial-gradient(circle at 60% 40%,#9e1525,var(--ruby) 60%,var(--ruby-dark))}
.footer-brand{left:0;top:3660px;width:1200px;text-align:center;color:#fff;font-size:35px;font-weight:700}
.footer-nav{left:0;top:3720px;width:1200px;display:flex;justify-content:center;gap:50px;color:#fff;font-size:20px}
.footer-rule{left:0;top:3776px;width:1200px;height:1px;background:rgba(255,255,255,.4)}
.copyright{left:0;top:3797px;width:1200px;text-align:center;color:#e8c4c8;font-size:14px}
</style>
</head>
<body>
<div class="abs topbar"></div>
<header class="abs header">
  <div class="abs brand">Garvel Pryce Transport</div>
  <nav class="abs nav">
    <span>Home</span><span>About Us</span><span>Services</span><span>Blog</span><span>Contact Us</span>
    <svg width="16" height="16" viewBox="0 0 16 16"><circle cx="6.5" cy="6.5" r="5" fill="none" stroke="#111" stroke-width="2"/><line x1="10.5" y1="10.5" x2="15" y2="15" stroke="#111" stroke-width="2"/></svg>
  </nav>
</header>

<section class="abs hero">
  <div class="abs hero-road" role="img" aria-label="Light trails on a winding night road"></div>
  <div class="abs hero-truck" role="img" aria-label="White and ruby articulated lorry"></div>
  <div class="abs hero-text">
    <div class="pre">Welcome To</div>
    <h1>Garvel Pryce Transport</h1>
    <p>Lorem ipsum dolor sit amet, consectetur adipiscing elit, sed do eiusmod tempor incididunt ut labore et dolore magna aliqua Quis ipsum suspendisse ultrices gravida.</p>
  </div>
</section>

<h2 class="abs section-title about-title">About Us</h2>
<p class="abs about-lead">Lorem ipsum dolor sit amet, consectetur adipiscing elit, sed do eiusmod tempor</p>
<p class="abs body-text about-p1">Sed ut perspiciatis unde omnis iste natus error sit voluptatem accusantium doloremque laudantium, totam rem aperiam, eaque ipsa quae ab illo inventore veritatis et quasi architecto beatae vitae dicta sunt explicabo.</p>
<p class="abs body-text about-p2">Nemo enim ipsam voluptatem quia voluptas sit aspernatur aut odit aut fugit, sed quia consequuntur magni dolores eosqui ratione voluptatem sequi nesciunt. Neque porro quisquam est, qui dolorem ipsum quia dolor sit amet, consectetur, adipisci velit, sed quia non numquam eius modi tempora incidunt ut labore et dolore magnam aliquam quaerat voluptatem.</p>
<div class="abs btn about-btn">Learn More</div>
<div class="abs about-frame"></div>
<div class="abs about-photo" role="img" aria-label="Two fleet lorries parked on a yard"></div>

<section class="abs services">
</section>
<h2 class="abs services-title">Our Services</h2>
<div class="abs card" style="left:110px;background:linear-gradient(180deg,#c9ccd0,#6c6f74)" role="img" aria-label="Lorry driving on a highway"></div>
<div class="abs card" style="left:446px;background:linear-gradient(180deg,#6b4a3a,#c4c24a)" role="img" aria-label="Warehouse staff checking paperwork"></div>
<div class="abs card" style="left:782px;background:linear-gradient(180deg,#b7cde0,#d9d9d9 55%,#9e9a90)" role="img" aria-label="Row of parked lorries"></div>
<div class="abs card-label" style="left:133px">Lorem Ipsum</div>
<div class="abs card-label" style="left:469px">Lorem Ipsum</div>
<div class="abs card-label" style="left:805px">Lorem Ipsum</div>
<svg class="abs arrow" style="left:34px" width="60" height="60" viewBox="0 0 60 60"><circle cx="30" cy="30" r="28" fill="none" stroke="#fff" stroke-width="2.5"/><polyline points="35,16 21,30 35,44" fill="none" stroke="#fff" stroke-width="2.5"/></svg>
<svg class="abs arrow" style="left:1106px" width="60" height="60" viewBox="0 0 60 60"><circle cx="30" cy="30" r="28" fill="none" stroke="#fff" stroke-width="2.5"/><polyline points="25,16 39,30 25,44" fill="none" stroke="#fff" stroke-width="2.5"/></svg>

<div class="abs why-frame"></div>
<div class="abs why-photo" role="img" aria-label="Lorries parked at night"></div>
<h2 class="abs section-title why-title">Why Choose Us</h2>
<p class="abs body-text why-p1">Sed ut perspiciatis unde omnis iste natus error sit voluptatem accusantium doloremque laudantium, totam rem aperiam, eaque ipsa quae ab illo inventore veritatis et quasi architecto beatae vitae dicta sunt explicabo.</p>
<p class="abs body-text why-p2">Nemo enim ipsam voluptatem quia voluptas sit aspernatur aut odit aut fugit, sed quia consequuntur magni dolores eosqui ratione voluptatem sequi nesciunt Neque porro quisquam est, qui dolorem ipsum quia dolor</p>
<div class="abs btn why-btn">Learn More</div>

<section class="abs testimonials"></section>
<h2 class="abs section-title testi-title">Testimonials</h2>
<div class="abs avatar" style="left:204px" role="img" aria-label="Customer portrait"></div>
<div class="abs avatar" style="left:532px" role="img" aria-label="Customer portrait"></div>
<div class="abs avatar" style="left:858px" role="img" aria-label="Customer portrait"></div>
<p class="abs quote" style="left:124px">Lorem ipsum dolor sit amet, consecte-tur adipiscing elit, sed do eiusmod tempor</p>
<p class="abs quote" style="left:450px">Lorem ipsum dolor sit amet, consecte-tur adipiscing elit, sed do eiusmod tempor</p>
<p class="abs quote" style="left:776px">Lorem ipsum dolor sit amet, consecte-tur adipiscing elit, sed do eiusmod tempor</p>
<div class="abs quote-name" style="left:124px">- John Peter</div>
<div class="abs quote-name" style="left:450px">- John Peter</div>
<div class="abs quote-name" style="left:776px">- John Peter</div>
<div class="abs dots"><span class="dot"></span><span class="dot"></span><span class="dot active"></span><span class="dot"></span></div>

<h2 class="abs section-title faq-title">Frequently Asked Questions</h2>
<div class="abs faq-rule"></div>
<div class="abs faq-line"></div>
<svg class="abs" style="left:111px;top:3130px" width="48" height="56" viewBox="0 0 48 56"><path d="M24 2a22 22 0 0 1 22 22c0 12-12 20-22 30C14 44 2 36 2 24A22 22 0 0 1 24 2z" fill="#8c1020"/><text x="24" y="32" text-anchor="middle" font-family="Roboto,Arial,sans-serif" font-size="22" font-weight="700" fill="#fff">?</text></svg>
<svg class="abs" style="left:111px;top:3280px" width="48" height="56" viewBox="0 0 48 56"><path d="M24 2a22 22 0 0 1 22 22c0 12-12 20-22 30C14 44 2 36 2 24A22 22 0 0 1 24 2z" fill="#bdbdbd"/><text x="24" y="32" text-anchor="middle" font-family="Roboto,Arial,sans-serif" font-size="22" font-weight="700" fill="#fff">?</text></svg>
<svg class="abs" style="left:111px;top:3364px" width="48" height="56" viewBox="0 0 48 56"><path d="M24 2a22 22 0 0 1 22 22c0 12-12 20-22 30C14 44 2 36 2 24A22 22 0 0 1 24 2z" fill="#bdbdbd"/><text x="24" y="32" text-anchor="middle" font-family="Roboto,Arial,sans-serif" font-size="22" font-weight="700" fill="#fff">?</text></svg>
<svg class="abs" style="left:111px;top:3448px" width="48" height="56" viewBox="0 0 48 56"><path d="M24 2a22 22 0 0 1 22 22c0 12-12 20-22 30C14 44 2 36 2 24A22 22 0 0 1 24 2z" fill="#bdbdbd"/><text x="24" y="32" text-anchor="middle" font-family="Roboto,Arial,sans-serif" font-size="22" font-weight="700" fill="#fff">?</text></svg>
<div class="abs faq-q" style="top:3148px">Lorem ipsum dolor sit amet, consectetur adipis ?</div>
<p class="abs faq-a">Lorem ipsum dolor sit amet, consectetur adipiscing elit, sed do eiusmod tempor incididunt ut labore et dolore magna aliqua. Quis ipsum suspendisse</p>
<div class="abs faq-q" style="top:3297px">Lorem ipsum dolor sit amet, consectetur adipis ?</div>
<div class="abs faq-q" style="top:3381px">Lorem ipsum dolor sit amet, consectetur adipis ?</div>
<div class="abs faq-q" style="top:3465px">Lorem ipsum dolor sit amet, consectetur adipis ?</div>
<div class="abs faq-art" role="img" aria-label="White speech bubbles with question marks"></div>

<footer class="abs footer"></footer>
<div class="abs footer-brand">Garvel Pryce Transport</div>
<nav class="abs footer-nav"><span>Home</span><span>About Us</span><span>Services</span><span>Blog</span><span>Contact Us</span></nav>
<div class="abs footer-rule"></div>
<div class="abs copyright">Copyright © 2024 Garvel Pryce Transport. All Rights Reserved</div>
</body>
</html>
```